Logo + Label Design (Men’s Grooming Brand & Product Packaging)

Design a logo and 2 oz pomade label for Brel, a modern men’s grooming brand focused on clean, high-quality, natural ingredients. The design should establish a bold, masculine, minimalist identity that can later extend to products like shaving gel and body wash.

Key Requirements

Create a primary logo for “Brel” and a core label for the 2 oz pomade jar (screw-top).

Use a clean, modern style — masculine, confident, and approachable (think Dorran’s, Velta, Northfield Kit).

Design for 1–2 color screen printing on solid jar colors (white, black, or navy).

Avoid gradients, foil, or embossing. Must work in black & white.

Provide: vector logo, mockup of the 2 oz jar, color palette (CMYK/RGB/HEX), and font specs.

Winning design may lead to future projects (body wash, shave gel, skincare lines).

Font styles to use
Other font styles liked:
• We like the fonts and design concept in the attached mockup.

Requirements
Should not have
• We want to avoid too much writing or busy designs. We want to avoid having graphics/illustrations embedded in the logo if they will cause the brand to look less classy or sophisticated. We also want the design to look simple and all-American (e.g. Hollister and Vane, Pine Ledger, The KIM, etc). We’d like to give a Pellham & Royce vibe that feels classy and high end.

```html
<!DOCTYPE html>
<html lang="en">
<head>
<meta charset="utf-8">
<title>Brel Hair Pomade Label</title>
<link href="https://fonts.googleapis.com/css2?family=Playfair+Display:wght@700;900&family=Crimson+Text:wght@400;600&display=swap" rel="stylesheet">
<style>
  :root {
    --backdrop: #e4e8ef;
    --jar-black: #141416;
    --ink-white: #eef0f5;
    --accent-blue: #2f80d8;
    --rule: #c9ccd3;
  }
  html, body {
    margin: 0;
    width: 1200px;
    height: 1200px;
    overflow: hidden;
    background: var(--backdrop);
  }
  .canvas {
    position: relative;
    width: 1200px;
    height: 1200px;
  }
  .serif-display { font-family: "Playfair Display", Georgia, serif; }
  .serif-text { font-family: "Crimson Text", Georgia, serif; }

  /* Lid label */
  .lid-label {
    position: absolute;
    left: 340px;
    top: 50px;
    width: 520px;
    height: 520px;
    border-radius: 50%;
    background: var(--jar-black);
    color: var(--ink-white);
    display: flex;
    align-items: center;
    justify-content: center;
    gap: 22px;
  }
  .vertical-title {
    writing-mode: vertical-rl;
    transform: rotate(180deg);
    font-family: "Crimson Text", Georgia, serif;
    font-weight: 600;
    font-size: 22px;
    letter-spacing: 0.5px;
  }
  .lid-label .divider { width: 24px; height: 170px; }
  .lid-stack { display: flex; flex-direction: column; }
  .wordmark {
    font-family: "Playfair Display", Georgia, serif;
    font-weight: 900;
    line-height: 0.9;
    color: var(--ink-white);
    letter-spacing: -1px;
  }
  .lid-stack .wordmark { font-size: 96px; }
  .lid-finish {
    font-family: "Playfair Display", Georgia, serif;
    font-weight: 700;
    font-size: 22px;
    line-height: 1;
    margin-top: 8px;
    letter-spacing: 1px;
  }
  .lid-scent {
    font-family: "Playfair Display", Georgia, serif;
    font-weight: 700;
    font-size: 22px;
    color: var(--accent-blue);
    margin-top: 10px;
    letter-spacing: 1px;
  }
  .net-weight {
    font-family: "Crimson Text", Georgia, serif;
    font-size: 15px;
    margin-top: 12px;
    letter-spacing: 1px;
  }

  /* Wrap label */
  .wrap-label {
    position: absolute;
    left: 50px;
    top: 650px;
    width: 1100px;
    height: 420px;
    background: var(--jar-black);
    color: var(--ink-white);
    display: flex;
    align-items: center;
    padding: 0 34px;
    box-sizing: border-box;
    gap: 26px;
  }
  .usage-copy {
    width: 300px;
    font-family: "Crimson Text", Georgia, serif;
    font-size: 15px;
    line-height: 1.45;
    text-align: justify;
  }
  .usage-copy p { margin: 0 0 22px; }
  .wrap-label .divider { width: 24px; height: 300px; flex: none; }
  .wrap-label .wordmark {
    font-size: 168px;
    width: 320px;
    text-align: center;
  }
  .product-info {
    display: flex;
    align-items: center;
    gap: 18px;
    height: 300px;
  }
  .product-info .vertical-title { font-size: 24px; }
  .product-details { display: flex; flex-direction: column; }
  .product-finish {
    font-family: "Crimson Text", Georgia, serif;
    font-weight: 600;
    font-size: 26px;
    line-height: 1.1;
  }
  .product-scent {
    font-family: "Crimson Text", Georgia, serif;
    font-weight: 600;
    font-size: 24px;
    color: var(--accent-blue);
    margin-top: 16px;
  }
  .product-details .net-weight { margin-top: 60px; font-size: 14px; }
  .benefit-box {
    border: 1.5px solid var(--rule);
    border-radius: 10px;
    padding: 14px 12px;
    font-family: "Crimson Text", Georgia, serif;
    font-size: 14px;
    line-height: 1.7;
    margin-left: auto;
  }
  .benefit-box ul { list-style: none; margin: 0; padding: 0; }
  .benefit-box li::before {
    content: "";
    display: inline-block;
    width: 5px;
    height: 5px;
    background: var(--ink-white);
    transform: rotate(45deg);
    margin-right: 8px;
    vertical-align: middle;
  }
</style>
</head>
<body>
<main class="canvas">

  <section class="lid-label" aria-label="Lid label">
    <span class="vertical-title">Hair Pomade</span>
    <svg class="divider" viewBox="0 0 24 170" aria-hidden="true">
      <g stroke="#eef0f5" stroke-width="1.5">
        <line x1="5" y1="0" x2="5" y2="70"/><line x1="12" y1="0" x2="12" y2="70"/><line x1="19" y1="0" x2="19" y2="70"/>
        <line x1="5" y1="100" x2="5" y2="170"/><line x1="12" y1="100" x2="12" y2="170"/><line x1="19" y1="100" x2="19" y2="170"/>
      </g>
      <rect x="8" y="80" width="8" height="8" fill="#eef0f5" transform="rotate(45 12 84)"/>
    </svg>
    <div class="lid-stack">
      <span class="wordmark">Brel</span>
      <span class="lid-finish">Matte Finish<br>Medium Hold</span>
      <span class="lid-scent">Fresh &amp; Clean</span>
      <span class="net-weight">2 oz ( 57 g )</span>
    </div>
  </section>

  <section class="wrap-label" aria-label="Jar wrap label">
    <div class="usage-copy">
      <p>Directions: Rub a small amount of pomade between hands and apply to damp hair (for sleeker look) or dry hair (for a matte look). For external use only. Avoid contact with eyes. If irritation occurs, discontinue use.</p>
      <p>Ingredients: Butyrospermum Parkii (Shea Butter), Cera Alba (Beeswax), Euphorbia Cerifera (Cera Bellina), Caprylic/Capric Triglyceride, Cocos Nucifera (Coconut Oil), Tocopherol (Vitamin E).</p>
    </div>

    <svg class="divider" viewBox="0 0 24 300" aria-hidden="true">
      <g stroke="#eef0f5" stroke-width="1.5">
        <line x1="5" y1="0" x2="5" y2="135"/><line x1="12" y1="0" x2="12" y2="135"/><line x1="19" y1="0" x2="19" y2="135"/>
        <line x1="5" y1="165" x2="5" y2="300"/><line x1="12" y1="165" x2="12" y2="300"/><line x1="19" y1="165" x2="19" y2="300"/>
      </g>
      <rect x="8" y="146" width="8" height="8" fill="#eef0f5" transform="rotate(45 12 150)"/>
    </svg>

    <span class="wordmark">Brel</span>

    <svg class="divider" viewBox="0 0 24 300" aria-hidden="true">
      <g stroke="#eef0f5" stroke-width="1.5">
        <line x1="5" y1="0" x2="5" y2="135"/><line x1="12" y1="0" x2="12" y2="135"/><line x1="19" y1="0" x2="19" y2="135"/>
        <line x1="5" y1="165" x2="5" y2="300"/><line x1="12" y1="165" x2="12" y2="300"/><line x1="19" y1="165" x2="19" y2="300"/>
      </g>
      <rect x="8" y="146" width="8" height="8" fill="#eef0f5" transform="rotate(45 12 150)"/>
    </svg>

    <div class="product-info">
      <span class="vertical-title">Hair Pomade</span>
      <div class="product-details">
        <span class="product-finish">Matte Finish<br>Medium Hold</span>
        <span class="product-scent">Fresh &amp; Clean</span>
        <span class="net-weight">2 oz ( 57 g )</span>
      </div>
    </div>

    <div class="benefit-box">
      <ul>
        <li>Natural Ingredients</li>
        <li>For All Hair Types</li>
        <li>Alcohol Free</li>
        <li>Non-Greasy</li>
        <li>Easy Washout</li>
        <li>Made in USA</li>
      </ul>
    </div>
  </section>

</main>
</body>
</html>
```